TalkHarbor - Language Coaching Services

Sleek, innovative, trendy design for Language Coaching business.

TalkHarbor is a new UK based company that provides Language Coaching services. We offer highly personalized on-line and face to face language courses. We also impart learning techniques workshops based on the latest neuroscience research for second-language acquisition.

Target Market(s)

See attached info

Industry/Entity Type

Consulting

Contact Information for Business Card

TalkHarbor
DaniaKV@talkharbor.co.uk
TalkHarbor.co.uk
London, UK

Font styles to use
Sans Serif

```html
<!DOCTYPE html>
<html lang="en">
<head>
<meta charset="UTF-8">
<title>TalkHarbor Business Card</title>
<link href="https://fonts.googleapis.com/css2?family=Montserrat:wght@400;700&family=Roboto:wght@400&display=swap" rel="stylesheet">
<style>
  :root {
    --page-bg: #e8e8e8;
    --card-white: #ffffff;
    --blue-light: #0cb5ec;
    --blue-mid: #0492cc;
    --blue-dark: #02619a;
    --brand-blue: #0a88c0;
    --text-grey: #555b60;
    --white: #ffffff;
  }
  * { box-sizing: border-box; margin: 0; padding: 0; }
  html, body {
    width: 1125px;
    height: 1200px;
    overflow: hidden;
    background: var(--page-bg);
  }
  .canvas {
    position: relative;
    width: 1125px;
    height: 1200px;
  }
  .card {
    position: absolute;
    left: 150px;
    width: 825px;
    height: 471px;
    border-radius: 28px;
    overflow: hidden;
  }
  .card-front {
    top: 98px;
    background: var(--card-white);
  }
  .card-back {
    top: 631px;
    background: radial-gradient(ellipse at 50% 45%, var(--blue-light) 0%, var(--blue-mid) 45%, var(--blue-dark) 100%);
  }
  .front-band {
    position: absolute;
    inset: 0;
  }
  .holder {
    position: absolute;
    top: 40px;
    right: 48px;
    text-align: right;
    color: var(--white);
    font-family: "Montserrat", sans-serif;
    font-weight: 700;
    letter-spacing: 1px;
  }
  .holder-name { font-size: 29px; line-height: 1.1; }
  .holder-role { font-size: 20px; line-height: 1.2; }
  .brand-mark {
    position: absolute;
    left: 146px;
    top: 126px;
    width: 134px;
    height: 134px;
    border: 10px solid var(--brand-blue);
    border-radius: 50%;
  }
  .brand-name {
    position: absolute;
    left: 46px;
    top: 262px;
    font-family: "Montserrat", sans-serif;
    font-weight: 400;
    font-size: 47px;
    color: var(--brand-blue);
    letter-spacing: 0.5px;
  }
  .contact-list {
    position: absolute;
    left: 48px;
    top: 352px;
    list-style: none;
    font-family: "Montserrat", sans-serif;
    font-size: 19px;
    color: var(--text-grey);
  }
  .contact-item {
    display: flex;
    align-items: center;
    height: 26.5px;
  }
  .contact-icon {
    width: 18px;
    height: 18px;
    margin-right: 13px;
    flex: none;
  }
  .back-ring {
    position: absolute;
    left: 281px;
    top: 90px;
    width: 264px;
    height: 264px;
    border: 17px solid var(--white);
    border-radius: 50%;
    display: flex;
    align-items: center;
    justify-content: center;
  }
  .back-name {
    font-family: "Montserrat", sans-serif;
    font-weight: 400;
    font-size: 33px;
    color: var(--white);
  }
  .back-url {
    position: absolute;
    left: 0;
    right: 0;
    top: 400px;
    text-align: center;
    font-family: "Roboto", sans-serif;
    font-size: 19px;
    letter-spacing: 6px;
    color: var(--white);
  }
</style>
</head>
<body>
<main class="canvas">
  <section class="card card-front">
    <svg class="front-band" width="825" height="471" viewBox="0 0 825 471" aria-hidden="true">
      <defs>
        <radialGradient id="frontBlue" cx="0.78" cy="0.42" r="0.6">
          <stop offset="0" stop-color="#0cb5ec"/>
          <stop offset="0.5" stop-color="#0592cd"/>
          <stop offset="1" stop-color="#02619a"/>
        </radialGradient>
      </defs>
      <path d="M346,0 C560,110 810,330 686,471 L825,471 L825,0 Z" fill="url(#frontBlue)"/>
    </svg>
    <div class="holder">
      <p class="holder-name">OWEN CARTER</p>
      <p class="holder-role">CEO/FOUNDER</p>
    </div>
    <div class="brand-mark"></div>
    <p class="brand-name">TalkHarbor</p>
    <ul class="contact-list">
      <li class="contact-item">
        <svg class="contact-icon" viewBox="0 0 18 18" aria-hidden="true"><rect x="4" y="0.5" width="10" height="17" rx="2" fill="none" stroke="#0a88c0" stroke-width="2"/><circle cx="9" cy="14.5" r="1" fill="#0a88c0"/></svg>
        614 382 9057
      </li>
      <li class="contact-item">
        <svg class="contact-icon" viewBox="0 0 18 18" aria-hidden="true"><rect x="1" y="4" width="16" height="11" fill="#0a88c0"/><path d="M1,4 L9,10 L17,4" fill="none" stroke="#ffffff" stroke-width="1.5"/></svg>
        info@talkharbor.co.uk
      </li>
      <li class="contact-item">
        <svg class="contact-icon" viewBox="0 0 18 18" aria-hidden="true"><circle cx="9" cy="9" r="8" fill="#0a88c0"/><path d="M1,9 H17 M9,1 C5,5 5,13 9,17 M9,1 C13,5 13,13 9,17" fill="none" stroke="#ffffff" stroke-width="1.2"/></svg>
        www.talkharbor.co.uk
      </li>
    </ul>
  </section>

  <section class="card card-back">
    <div class="back-ring">
      <p class="back-name">TalkHarbor</p>
    </div>
    <p class="back-url">www.talkharbor.co.uk</p>
  </section>
</main>
</body>
</html>
```